New B2C website design to help dads be better dads

DadHarbor is a website to help dads be the “best dad you can be.”

We require our website to be designed into a PSD format, no coding necessary.

The general concept is a two-page design. The first page is the login page, the second page is the home page. Once at the home page, rather than navigating to and from different pages, the user will push and pull through different visual and functional layers of the hierarchy. In theory, this should add to the user experience by having a visual anchor of where they are (through layered pagination) as well as improving loading times since the new information should only be a delta in data load versus a brand new page load.

The general look-and-feel we are going for is clean, simple, minimal. This means that the winning design will show us a good eye for web-optimized typography, good use of white (negative) space, and good use of a visually pleasing grid.

We require a total of 6 page "views" plus the landing page. We note that many of the views are similar to one another.
Landing page
Milestone view
Task view
Content view, articles
Content view, products
Search view
What's new view

Please review all of the additional information provided as well as the attachments for examples.

We provide the following websites as good references for:

Typography:
http://example-kelvorn.com/journal/

Use of white space:
http://www.trenvaskit.com/
http://moldrefin.com/

Example for “scrolling” page concept as well as good balance of color, typography, and white space:
http://www.qorbitalmeet.eu/

Please contact us with questions so that we can guide your design effort.
Updates

Hello designers,

The following information is added to help guide the design process:

1.  For the text dialogue below the landing page, please assume the following word count:
"why are we making dad harbor?": 250 words
"who are we?" 200 words
"what's the deal with the penguin logo?" 300 words

For the social media links, please see http://www.gravelplumbs.com/
Notice the floating "social" bar that is always to the right.  This is the concept we are going for, please try to implement this as you see fit. 

Target Market(s)

Fathers of young children ages 0-6 years old.

Industry/Entity Type

Product

Font styles to use
Sans Serif

Requirements
Must have
• Clean lines, minimal design concept

Incorporation of our logo (see attached document)

Header content is static for all views after landing page, see example

This page WILL be responsive, please keep that in mind when designing
The timeline bar should be to the left, with the timeline bar’s “milestones” also being responsive.

Designer is free to suggest font types, but any fonts used must be royalty-free and web-optimized. We request a minimum number of font types as well as fonts that load relatively fast. We reinforce that visually appealing typography is a significant factor in the winning design choice.

While we are not expecting the winning design to include code, please keep in mind that the final implementation needs to be optimized for desktop, tablet, and mobile platforms.

If you are using stock photography that is not generated by you, please provide where/how we can obtain imagery, as well as price.

All custom graphics must be available in original formats; Photoshop/GIMP layered files for layout design, and vector formats for logos, icons and other graphical elements.

Please incorporate “Blue” into design elements as you see fit, as the RGB 67 74 169 Blue is the primary color used in our brand. The complement to this blue is 255 202 0, a brownish orange. Feel free to use this color as well, although please keep it to a lesser amount.

Background color is your choice, do not feel the need to use the grey.
Should not have
• Excessive graphical content such that it affects loading times

Excessive use of too many font types such that it affects loading times

```html
<!DOCTYPE html>
<html lang="en">
<head>
<meta charset="utf-8">
<title>DadHarbor – Sign in</title>
<link rel="stylesheet" href="https://fonts.googleapis.com/css2?family=Open+Sans:wght@300;400;600&family=Source+Sans+3:ital,wght@0,400;0,600;1,400&display=swap">
<style>
  :root {
    --page-bg: #f0f0f0;
    --surface: #ffffff;
    --brand-blue: #434aa9;
    --link-blue: #2f6db8;
    --button-top: #3f86d4;
    --button-bottom: #2363b0;
    --ink: #1b1b1b;
    --ink-soft: #3a3a3a;
    --heading-grey: #555555;
    --rule: #d4d4d4;
    --field-border: #a9a9a9;
    --footer-bg: #5a5a5a;
    --footer-edge: #8a8a8a;
    --footer-text: #ffffff;
    --sky: #e3e8f1;
    --sea-mid: #5d7d9a;
    --sea-deep: #2f4b66;
  }
  * { box-sizing: border-box; margin: 0; padding: 0; }
  html, body { width: 1200px; height: 1179px; overflow: hidden; }
  body {
    background: var(--page-bg);
    font-family: "Source Sans 3", sans-serif;
    color: var(--ink);
    position: relative;
  }
  .page {
    position: absolute; left: 181px; top: 0;
    width: 840px; height: 1179px;
    background: var(--surface);
  }
  /* Header */
  .brand {
    position: absolute; left: 21px; top: 62px;
    display: flex; align-items: center; gap: 8px;
    font-family: "Source Sans 3", sans-serif;
    font-weight: 600; font-size: 20px; color: var(--brand-blue);
  }
  .brand-dot { width: 14px; height: 14px; border-radius: 50%; background: var(--brand-blue); }
  .login-label {
    position: absolute; left: 360px; top: 32px;
    font-size: 11.5px; color: var(--link-blue); letter-spacing: .2px;
  }
  .field {
    position: absolute; top: 59px; width: 182px; height: 29px;
    border: 1px solid var(--field-border); border-radius: 3px;
    font-size: 10px; color: var(--ink-soft);
    padding: 9px 0 0 13px;
  }
  .field-user { left: 360px; }
  .field-pass { left: 557px; }
  .sign-in {
    position: absolute; left: 755px; top: 60px; width: 69px; height: 27px;
    border-radius: 3px; color: #fff; font-size: 11px; text-align: center; line-height: 27px;
    background: linear-gradient(var(--button-top), var(--button-bottom));
  }
  .help-link {
    position: absolute; top: 99px; font-size: 9.5px; font-style: italic; color: var(--ink-soft);
  }
  .help-forgot { left: 687px; }
  .help-request { left: 760px; }
  /* Hero */
  .hero {
    position: absolute; left: 0; top: 128px; width: 840px; height: 529px;
    background: linear-gradient(180deg, var(--sky) 0%, #b5c4d6 18%, var(--sea-mid) 45%, var(--sea-deep) 100%);
  }
  .hero-title {
    position: absolute; left: 375px; top: 49px;
    font-family: "Open Sans", sans-serif; font-weight: 400; font-size: 31px; color: var(--ink);
  }
  .hero-sub {
    position: absolute; left: 375px; top: 90px;
    font-family: "Open Sans", sans-serif; font-weight: 300; font-size: 20.5px; color: var(--ink);
  }
  .hero-text {
    position: absolute; left: 376px; top: 126px; width: 440px;
    font-size: 10.5px; line-height: 21.4px; color: var(--ink);
  }
  .hero-cta {
    position: absolute; left: 0; top: 443px; width: 840px; text-align: center;
    font-family: "Open Sans", sans-serif; font-weight: 300; font-size: 27px; color: #fff;
  }
  .scroll-button {
    position: absolute; left: 386px; top: 489px; width: 68px; height: 68px;
    border-radius: 50%; background: var(--surface);
    display: flex; align-items: flex-start; justify-content: center; padding-top: 21px;
  }
  /* About */
  .about-title {
    position: absolute; left: 0; top: 692px; width: 840px; text-align: center;
    font-family: "Open Sans", sans-serif; font-weight: 300; font-size: 33px; color: var(--link-blue);
  }
  .about-block { position: absolute; left: 29px; width: 783px; }
  .about-why { top: 770px; }
  .about-who { top: 922px; }
  .about-heading {
    font-family: "Open Sans", sans-serif; font-weight: 300; font-size: 25.5px; color: var(--heading-grey);
    margin-bottom: 14px;
  }
  .about-text { font-size: 9.8px; line-height: 21.4px; color: var(--ink-soft); }
  .about-rule { position: absolute; left: 29px; top: 908px; width: 783px; height: 1px; background: var(--rule); }
  /* Footer */
  .footer {
    position: absolute; left: 0; top: 1069px; width: 840px; height: 110px;
    background: var(--footer-bg); border-top: 2px solid var(--footer-edge);
    color: var(--footer-text);
  }
  .footer-nav { position: absolute; left: 31px; top: 29px; display: flex; font-size: 9.5px; }
  .footer-nav span { white-space: nowrap; }
  .footer-nav .sep { margin: 0 15px; }
  .copyright { position: absolute; left: 31px; top: 60px; font-size: 9.5px; }
  .social { position: absolute; left: 730px; top: 40px; display: flex; gap: 8px; }
  .social span { width: 22px; height: 22px; border-radius: 50%; background: var(--surface); }
</style>
</head>
<body>
<div class="page">
  <header>
    <div class="brand"><span class="brand-dot"></span>DadHarbor</div>
    <div class="login-label">USER LOGIN</div>
    <div class="field field-user">User name :</div>
    <div class="field field-pass">Password :</div>
    <div class="sign-in">Sign in</div>
    <div class="help-link help-forgot">Forgot login?</div>
    <div class="help-link help-request">Request access</div>
  </header>

  <section class="hero" role="img" aria-label="Photo of a father and young son on a pier, arms spread wide, facing the open sea">
    <h1 class="hero-title">Be the best Dad you can be</h1>
    <p class="hero-sub">The portal created exclusively for dads, by dads</p>
    <p class="hero-text">The general concept is a two-page design. The first page is the login page, the second page is the home page. Once at the home page, rather than navigating to and from different pages, the user will push and pull through different visual and functional layers of the hierarchy. In theory, this should add to the user experience by having a visual...</p>
    <p class="hero-cta">Learn about Dad Harbor</p>
    <div class="scroll-button">
      <svg width="20" height="12" viewBox="0 0 20 12"><polyline points="2,2 10,10 18,2" fill="none" stroke="#666" stroke-width="3"/></svg>
    </div>
  </section>

  <h2 class="about-title">About Dad Harbor</h2>
  <div class="about-block about-why">
    <h3 class="about-heading">Why are we making Dad Harbor?</h3>
    <p class="about-text">Lorem ipsum dolor sit amet, consectetur adipisicing elit, sed do eiusmod tempor incididunt ut labore et dolore magna aliqua. Ut enim ad minim veniam, quis nostrud exercitation ullamco laboris nisi ut aliquip ex ea commodo consequat. Duis aute irure dolor in reprehenderit in voluptate velit esse cillum dolore eu fugiat nulla pariatur. Excepteur sint occaecat cupidatat non proident, sunt in culpa qui officia deserunt mollit anim id est laborum</p>
  </div>
  <div class="about-rule"></div>
  <div class="about-block about-who">
    <h3 class="about-heading">Who are we?</h3>
    <p class="about-text">Lorem ipsum dolor sit amet, consectetur adipisicing elit, sed do eiusmod tempor incididunt ut labore et dolore magna aliqua. Ut enim ad minim veniam, quis nostrud exercitation ullamco laboris nisi ut aliquip ex ea commodo consequat. Duis aute irure dolor in reprehenderit in voluptate velit esse cillum dolore eu fugiat nulla pariatur. Excepteur sint occaecat cupidatat non proident, sunt in culpa qui officia deserunt mollit anim id est laborum</p>
  </div>

  <footer class="footer">
    <nav class="footer-nav">
      <span>Home</span><span class="sep">|</span>
      <span>About</span><span class="sep">|</span>
      <span>Prepare for the baby arrival</span><span class="sep">|</span>
      <span>What's the latest?</span><span class="sep">|</span>
      <span>Car Seats</span>
    </nav>
    <p class="copyright">Copyright 2013. Dad Harbor. All rights reserved.</p>
    <div class="social" aria-label="Social links"><span></span><span></span><span></span></div>
  </footer>
</div>
</body>
</html>
```